Professional and creative business card design for recruiting service providers

Our company supports German medium-sized companies in filling vacancies promptly. For this we use social media marketing and bring our customers into the visibility.

We want a professional but also creative design for our business cards.

Please look at lindqvar-staff.de to get an impression of our CI.

Target Market(s)

Small and medium-sized companies in Germany from the industry

Industry/Entity Type

Industrie, Handwerk

Contact Information for Business Card

Name, Position, Telefonnummer, Email, Website

Colors
EE7325
F08F49
F5BC92
FAE3D3
FDF4ED

Requirements
Must have
• A picture of the employee and in the style of www.lindqvar-staff.de

```html
<!DOCTYPE html>
<html lang="de">
<head>
<meta charset="utf-8">
<title>Lindqvar &amp; Staff – Visitenkarte</title>
<link href="https://fonts.googleapis.com/css2?family=Montserrat:wght@700;800&family=Poppins:wght@400;500&display=swap" rel="stylesheet">
<style>
  :root {
    --orange: #EE7325;
    --orange-light: #F08F49;
    --peach: #F5BC92;
    --ink: #111111;
    --paper: #F7F7F7;
    --backdrop: #DEDEDE;
    --photo-wall: #E6E3E3;
    --photo-suit: #3A3B40;
  }
  * { box-sizing: border-box; margin: 0; padding: 0; }
  html, body { width: 1200px; height: 930px; overflow: hidden; }
  body {
    background: var(--backdrop);
    font-family: "Poppins", Arial, sans-serif;
    position: relative;
  }
  .card {
    position: absolute;
    width: 560px;
    height: 320px;
    box-shadow: 0 14px 30px rgba(0,0,0,0.18);
  }
  /* Back side */
  .card--back {
    left: 580px;
    top: 110px;
    background: var(--ink);
    display: flex;
    align-items: center;
    justify-content: center;
    gap: 22px;
  }
  .brand { display: flex; align-items: center; }
  .brand__mark { flex: none; }
  .brand__name {
    font-family: "Montserrat", Arial, sans-serif;
    font-weight: 800;
    text-transform: uppercase;
    letter-spacing: 0.06em;
    line-height: 1.05;
  }
  .card--back .brand { gap: 22px; }
  .card--back .brand__mark { width: 58px; height: 58px; background: #FFFFFF; }
  .card--back .brand__name { color: #FFFFFF; font-size: 30px; }

  /* Front side */
  .card--front {
    left: 60px;
    top: 500px;
    background: var(--paper);
    padding: 34px 36px;
  }
  .card--front .brand { gap: 16px; }
  .card--front .brand__mark { width: 44px; height: 44px; background: var(--orange); }
  .card--front .brand__name { color: var(--ink); font-size: 22px; }
  .person { margin-top: 24px; }
  .person__name {
    font-family: "Montserrat", Arial, sans-serif;
    font-weight: 700;
    font-size: 19px;
    letter-spacing: 0.05em;
    text-transform: uppercase;
    color: var(--ink);
  }
  .person__role {
    font-size: 14px;
    color: var(--orange);
    margin-top: 2px;
  }
  .contact { list-style: none; margin-top: 16px; }
  .contact__item {
    display: flex;
    align-items: center;
    gap: 8px;
    font-size: 13px;
    color: var(--ink);
    line-height: 1.65;
  }
  .contact__icon { width: 12px; height: 12px; flex: none; }
  .portrait {
    position: absolute;
    right: 34px;
    bottom: 30px;
    width: 220px;
    height: 200px;
    border: 2px solid var(--ink);
    background: linear-gradient(180deg, var(--photo-wall) 0%, var(--photo-wall) 55%, var(--photo-suit) 100%);
  }
</style>
</head>
<body>

  <section class="card card--back" aria-label="Rückseite">
    <div class="brand">
      <span class="brand__mark"></span>
      <span class="brand__name">Lindqvar<br>&amp; Staff</span>
    </div>
  </section>

  <section class="card card--front" aria-label="Vorderseite">
    <div class="brand">
      <span class="brand__mark"></span>
      <span class="brand__name">Lindqvar<br>&amp; Staff</span>
    </div>

    <div class="person">
      <p class="person__name">Henrik Aldemann</p>
      <p class="person__role">Managing Director</p>
    </div>

    <ul class="contact">
      <li class="contact__item">
        <svg class="contact__icon" viewBox="0 0 24 24"><path fill="var(--orange)" d="M6.6 10.8a15 15 0 0 0 6.6 6.6l2.2-2.2c.3-.3.7-.4 1-.2 1.1.4 2.3.6 3.6.6.6 0 1 .4 1 1V20c0 .6-.4 1-1 1A17 17 0 0 1 3 4c0-.6.4-1 1-1h3.5c.6 0 1 .4 1 1 0 1.3.2 2.5.6 3.6.1.3 0 .7-.2 1z"/></svg>
        040-987 654 321
      </li>
      <li class="contact__item">
        <svg class="contact__icon" viewBox="0 0 24 24"><rect x="2" y="5" width="20" height="14" fill="var(--orange)"/><path d="M2 5l10 8 10-8" fill="none" stroke="#FFFFFF" stroke-width="2"/></svg>
        info@lindqvar-staff.de
      </li>
      <li class="contact__item">
        <svg class="contact__icon" viewBox="0 0 24 24"><circle cx="12" cy="12" r="10" fill="var(--orange)"/><path d="M2 12h20M12 2c3 3 3 17 0 20M12 2c-3 3-3 17 0 20" fill="none" stroke="#FFFFFF" stroke-width="1.4"/></svg>
        www.lindqvar-staff.de
      </li>
    </ul>

    <div class="portrait" role="img" aria-label="Porträtfoto des Mitarbeiters im dunklen Sakko vor hellem Hintergrund"></div>
  </section>

</body>
</html>
```